Workshop PPT Update for AI Transformation Sessions

Our strategic consulting firm runs strategy workshops using slides as workshop exercises. These slides are used to communicate to the participants in advance, run the workshops and produce the final deliverable.

It is time for a design "upgrade". We'd like them to be more engaging, hipper and more interesting. These slides are utilitarian, so clean and usable is good. I have attached the example of what we have today. I have also attached an example of another company's slides that I like.

We can't rip off their design nor can we go away 100% from what we have. But I think it is possible to "update" our look to something closer to their look. Grey colors are fine with some color pop.

Slide styles needed are - 1) Cover Page, 2) Instructions Page, 3) Bullet list 4) Worksheet (place for participants to add content 5) Table, 6) Two column.

```html
<!DOCTYPE html>
<html lang="en">
<head>
<meta charset="utf-8">
<title>NorthPath Workshop Slide System</title>
<link rel="stylesheet" href="https://fonts.googleapis.com/css2?family=Montserrat:wght@400;500;600;700&display=swap">
<style>
:root{
  --slate:#4b4f60;
  --slate-dark:#3e4252;
  --red:#a9423f;
  --red-frame:#b8403d;
  --white:#ffffff;
  --paper:#ffffff;
  --ink:#2b2d36;
  --card-text:#3d404c;
}
*{box-sizing:border-box;margin:0;padding:0}
html,body{width:1200px;height:540px;overflow:hidden;background:var(--paper);font-family:"Montserrat",sans-serif;color:var(--white)}
.board{position:relative;width:1200px;height:540px}
.card{position:absolute;width:346px;height:194px;background:var(--white);box-shadow:0 2px 10px rgba(0,0,0,.12)}
.slide{position:absolute;left:16px;top:16px;width:315px;height:161px;border:2px solid var(--red-frame);background:var(--slate);overflow:hidden}
.footer{position:absolute;left:16px;top:184px;font-size:3.4px;font-weight:600;color:var(--ink)}
.page{position:absolute;right:17px;top:182px;width:6px;height:6px;border-radius:50%;background:var(--red);font-size:3px;color:var(--white);text-align:center;line-height:6px;font-weight:700}
.brand{position:absolute;font-weight:500;letter-spacing:-.2px;color:var(--white)}
.brand .dot{display:inline-block;width:.55em;height:.55em;border-radius:50%;background:var(--red);margin-right:2px;vertical-align:.05em}
.abs{position:absolute}
.cap{text-transform:uppercase;letter-spacing:.8px;font-weight:700}

/* cover */
.cover-photo{position:absolute;left:181px;top:-30px;width:200px;height:220px;border-radius:50%;background:linear-gradient(160deg,#8a8f9a,#4d5160 60%,#6d6f78);border-left:4px solid var(--white)}
.cover-title{left:37px;top:58px;font-size:8.5px}
.cover-list{position:absolute;left:38px;top:78px;list-style:none}
.cover-list li{font-size:4.4px;font-weight:600;height:13px;display:flex;align-items:center;gap:5px}
.cover-list li::before{content:"✦";font-size:7px}

/* kickoff */
.kick-photo{position:absolute;inset:0;background:linear-gradient(120deg,#3d4a3f,#6a6e78 35%,#8c8f96 60%,#5b5e68)}
.kick-shade{position:absolute;inset:0;background:rgba(62,66,82,.55)}
.kick-text{position:absolute;left:0;right:0;text-align:center}

/* table */
.plan{position:absolute;left:21px;top:31px;width:272px;border-collapse:collapse;font-size:4.6px;font-weight:600;text-align:center}
.plan td{border:1px solid rgba(255,255,255,.85);padding:0 2px;line-height:1.2}
.plan .hot{background:var(--red)}

/* overview panels */
.split-left{position:absolute;left:0;top:0;width:217px;height:100%;background:var(--slate)}
.split-right{position:absolute;left:217px;top:0;right:0;height:100%;background:var(--red)}
.steps{position:absolute;left:20px;top:28px;list-style:none}
.steps li{position:relative;padding-left:13px;margin-bottom:7px}
.steps .num{position:absolute;left:0;top:0;font-size:5px}
.steps .head{font-size:5.3px;font-weight:500;text-transform:uppercase}
.steps .sub{font-size:3.3px;text-transform:uppercase;margin-top:3px}
.panel-title{font-size:9.5px;line-height:1.35}
.mini{position:absolute;border:1px solid rgba(255,255,255,.85);display:grid;grid-template-columns:1fr 1fr;font-size:4px;font-weight:700;text-align:center}
.mini div{border:.5px solid rgba(255,255,255,.5);padding:3px 1px}
.prep{position:absolute;list-style:none}
.prep li{font-size:4.2px;text-transform:uppercase;height:10.8px;display:flex;align-items:center;gap:4px}
.prep li::before{content:"";width:4px;height:4px;border:.8px solid rgba(255,255,255,.8);border-radius:50%}

/* flow */
.flow-card{position:absolute;width:66px;height:48px;background:rgba(255,255,255,.9);color:var(--card-text);font-size:4.6px;font-weight:600;display:flex;align-items:center;justify-content:center;text-align:center;padding:4px;line-height:1.4}
.check li{text-transform:none;font-size:4.3px}

/* principles */
.ai-note{font-size:3.1px;line-height:1.3}
</style>
</head>
<body>
<main class="board">

  <!-- Cover -->
  <section class="card" style="left:57px;top:56px">
    <div class="slide">
      <div class="cover-photo" role="img" aria-label="Photo of two businessmen reviewing a document"></div>
      <div class="brand" style="left:37px;top:35px;font-size:10px"><span class="dot"></span>NorthPath</div>
      <h1 class="abs cap cover-title">Getting Started</h1>
      <ul class="cover-list">
        <li>Complete the Engagement Sizing Survey.</li>
        <li>Collect relevant inputs.</li>
        <li>Determine workshop participants &amp; date.</li>
        <li>Send invites, to include pre-work.</li>
      </ul>
    </div>
    <p class="footer">© 2024 NorthPath. All Rights Reserved. Privacy Policy and Terms</p>
    <span class="page">1</span>
  </section>

  <!-- Kickoff -->
  <section class="card" style="left:438px;top:56px">
    <div class="slide">
      <div class="kick-photo" role="img" aria-label="Photo of three colleagues discussing at a laptop"></div>
      <div class="kick-shade"></div>
      <div class="kick-text" style="top:58px;font-size:10px;font-weight:500"><span class="brand" style="position:static"><span class="dot"></span>NorthPath</span></div>
      <h1 class="kick-text cap" style="top:75px;font-size:10px">Kickoff &amp; Discovery</h1>
      <p class="kick-text" style="top:95px;font-size:5.2px;font-weight:600;letter-spacing:.4px">Sizing &amp; Scoping AI Transformation</p>
    </div>
    <p class="footer" style="top:182px">© 2024 NorthPath. All Rights Reserved. Privacy Policy and Terms</p>
    <span class="page" style="top:180px">3</span>
  </section>

  <!-- Plan structure -->
  <section class="card" style="left:818px;top:56px">
    <div class="slide">
      <div class="brand" style="left:17px;top:9px;font-size:10px">NorthPath</div>
      <h1 class="abs cap" style="right:28px;top:11px;font-size:9.5px">Plan Structure</h1>
      <table class="plan">
        <tr style="height:23px"><td colspan="2" style="font-size:6px">Level</td><td>Planning Element<br>&amp; Definition</td><td>Accountability<br>/Owner</td><td>Frequency<br>of Modification</td></tr>
        <tr style="height:22px"><td style="width:34px">1</td><td style="width:43px">What<br>(overall)</td><td style="width:59px">Strategic Priorities</td><td style="width:63px">N/A</td><td>3+ years</td></tr>
        <tr style="height:24px"><td>1.1</td><td>What<br>(this year)</td><td>Goals Outcomes<br>&amp; Strategies</td><td>Executive<br>Leadership</td><td>1-3 years</td></tr>
        <tr style="height:28px"><td>1.1.1</td><td>How</td><td>Goals Outcomes<br>&amp; Strategies</td><td class="hot"></td><td>1 year<br>(w/ qrtly targets)</td></tr>
        <tr style="height:28px"><td>1.1.1.1</td><td>How</td><td>Action Items</td><td class="hot"></td><td>Quarterly/Monthly</td></tr>
      </table>
    </div>
    <p class="footer" style="top:182px">© 2024 NorthPath. All Rights Reserved. Privacy Policy and Terms</p>
    <span class="page" style="top:180px">9</span>
  </section>

  <!-- Workshop overview -->
  <section class="card" style="left:57px;top:288px">
    <div class="slide">
      <div class="split-left">
        <div class="brand" style="left:20px;top:5px;font-size:10px">NorthPath</div>
        <ol class="steps">
          <li><span class="num">1</span><div class="head">Confirm Company Direction</div><div class="sub">Recap organizational purpose, values, vision &amp; winning strategy.</div></li>
          <li><span class="num">2</span><div class="head">Develop AI Vision</div></li>
          <li><span class="num">3</span><div class="head">Develop AI Guiding Principles</div><div class="sub">Developed AI guiding principles, supporting policies to inc approved.</div></li>
          <li><span class="num">4</span><div class="head">Agree on a Governance Approach</div><div class="sub">Agreed upon governance approach, structure &amp; executive champion.</div></li>
          <li><span class="num">5</span><div class="head">Agree on a Training &amp; Learning Approach</div><div class="sub">Set approach to training &amp; continuous learning.</div></li>
          <li><span class="num">6</span><div class="head">Determine Rollout &amp; Communication</div><div class="sub">Organizational rollout &amp; continuous communication.</div></li>
        </ol>
      </div>
      <div class="split-right">
        <h2 class="abs cap panel-title" style="left:16px;top:18px">Workshop<br>Overview</h2>
        <div class="mini" style="left:8px;top:52px;width:78px">
          <div>PARTICIPANTS</div><div>EXECS</div>
          <div>◷</div><div>▤</div>
          <div>2 HRS</div><div>DURATION</div>
        </div>
        <h3 class="abs cap" style="left:8px;top:102px;font-size:6px">Prep Work:</h3>
        <ul class="prep" style="left:12px;top:114px">
          <li>Org Strategy</li><li>2023 Goal Performance</li><li>Existing Policies</li><li>Pre-thinking Questions</li>
        </ul>
      </div>
    </div>
    <p class="footer">© 2024 NorthPath. All Rights Reserved. Privacy Policy and Terms</p>
    <span class="page">11</span>
  </section>

  <!-- Workshop flow -->
  <section class="card" style="left:438px;top:288px">
    <div class="slide">
      <div class="split-left">
        <div class="brand" style="left:6px;top:14px;font-size:10px">NorthPath</div>
        <h1 class="abs cap" style="left:112px;top:16px;font-size:9px">Workshop Flow</h1>
        <div class="flow-card" style="left:6px;top:37px">Determine the topics that need a principle.</div>
        <div class="flow-card" style="left:77px;top:37px">Look at the current policies to determine if all topics.</div>
        <div class="flow-card" style="left:147px;top:37px">Finalize via a legal and executive review.</div>
        <div class="flow-card" style="left:6px;top:98px">Determine which GPs need detailed policies.</div>
        <div class="flow-card" style="left:77px;top:98px">Determine which AI Tools support the GPs.</div>
        <div class="flow-card" style="left:147px;top:98px">Draft the Guiding Principles.</div>
      </div>
      <div class="split-right">
        <h2 class="abs cap panel-title" style="left:16px;top:18px">Workshop<br>Overview</h2>
        <p class="abs" style="left:7px;top:60px;font-size:4.2px;font-weight:700">PARTICIPANTS</p>
        <p class="abs" style="left:48px;top:60px;font-size:4.2px;font-weight:700">AI CHAT PROMPTS</p>
        <p class="abs" style="left:12px;top:72px;font-size:4.2px;font-weight:600">See next<br>slides</p>
        <p class="abs" style="left:63px;top:75px;font-size:4.2px;font-weight:600">Here</p>
        <h3 class="abs cap" style="left:8px;top:104px;font-size:5.2px">Your Existing Material:</h3>
        <ul class="prep check" style="left:13px;top:115px">
          <li>Company Values</li><li>Current Policies (GDPR,CCPA.)</li><li>Legal Guidance</li><li>OTHER</li>
        </ul>
      </div>
    </div>
    <p class="footer" style="top:182px">© 2024 NorthPath. All Rights Reserved. Privacy Policy and Terms</p>
    <span class="page">12</span>
  </section>

  <!-- AI guiding principles -->
  <section class="card" style="left:818px;top:288px">
    <div class="slide">
      <div class="split-left">
        <div class="brand" style="left:0;right:0;text-align:center;top:14px;font-size:10px">NorthPath</div>
        <svg class="abs" style="left:0;top:0" width="217" height="161" viewBox="0 0 217 161" aria-hidden="true">
          <g fill="#a9423f" stroke="#fff" stroke-width="1.2">
            <circle cx="109" cy="81" r="17"/>
            <circle cx="76" cy="55" r="13"/>
            <circle cx="142" cy="55" r="11"/>
            <circle cx="76" cy="107" r="10"/>
            <circle cx="142" cy="105" r="13"/>
          </g>
          <g fill="#fff" font-family="Montserrat, sans-serif" text-anchor="middle">
            <text x="109" y="83" font-size="5.5" font-weight="500">NorthPath</text>
            <text x="76" y="52" font-size="3">Principle</text><text x="76" y="62" font-size="9" font-weight="700">1</text>
            <text x="142" y="52" font-size="3">Principle</text><text x="142" y="61" font-size="8.5" font-weight="700">3</text>
            <text x="76" y="104" font-size="3">Principle</text><text x="76" y="113" font-size="8.5" font-weight="700">2</text>
            <text x="142" y="102" font-size="3">Principle</text><text x="142" y="111" font-size="9" font-weight="700">4</text>
          </g>
        </svg>
        <p class="abs ai-note" style="left:6px;top:43px;width:56px;text-align:right">Complete perspective from Executives, Directors, Managers &amp; Staff. Conduct competitive analysis and customer research (optional).</p>
        <p class="abs ai-note" style="left:158px;top:43px;width:56px">Complete perspective from Executives, Directors, Managers &amp; Staff. Conduct competitive analysis and customer research (optional).</p>
        <p class="abs ai-note" style="left:6px;top:98px;width:56px;text-align:right">Complete perspective from Executives, Directors, Managers &amp; Staff. Conduct competitive analysis and customer research (optional).</p>
        <p class="abs ai-note" style="left:161px;top:98px;width:54px">Complete perspective from Executives, Directors, Managers &amp; Staff. Conduct competitive analysis and customer research (optional).</p>
        <p class="abs ai-note" style="left:20px;top:141px;width:180px;text-align:center">Complete perspective from Executives, Directors, Managers &amp; Staff. Conduct competitive analysis and customer research (optional).</p>
      </div>
      <div class="split-right">
        <h2 class="abs cap" style="left:0;right:0;text-align:center;top:48px;font-size:9.5px;line-height:1.2">AI Guiding<br>Principles</h2>
        <p class="abs" style="left:0;right:0;text-align:center;top:88px;font-size:6px;font-weight:700;line-height:1.8">What guides our<br>decision-making<br>and<br>approach?</p>
      </div>
    </div>
    <p class="footer" style="top:183px">© 2024 NorthPath. All Rights Reserved. Privacy Policy and Terms</p>
    <span class="page" style="top:181px">22</span>
  </section>

</main>
</body>
</html>
```